VOMRA Pty Ltd Business Card

Looking for a simple yet eye-catching double-sided business card design using my company logo on one side and contact details on the other.

Target Market(s)

Government

Industry/Entity Type

Communication Systems Engineering

Contact Information for Business Card

VOMRA Pty Ltd

Requirements
Nice to have
• Would be great to have a QR code so details can be scanned into contacts

```html
<!DOCTYPE html>
<html lang="en">
<head>
<meta charset="utf-8">
<title>VOMRA Pty Ltd Business Card</title>
<link rel="stylesheet" href="https://fonts.googleapis.com/css2?family=Open+Sans:wght@400;600;700&display=swap">
<style>
  :root {
    --ink: #363e45;
    --paper: #ffffff;
    --stage: #2b2f33;
    --rule: #2a2f34;
  }
  * { box-sizing: border-box; margin: 0; padding: 0; }
  html, body { width: 1200px; height: 780px; overflow: hidden; }
  body {
    background: var(--stage);
    font-family: "Open Sans", sans-serif;
    position: relative;
  }
  .card {
    position: absolute;
    top: 236px;
    width: 540px;
    height: 308px;
    border-radius: 22px;
    overflow: hidden;
  }
  .card-front { left: 40px; background: var(--ink); }
  .card-back { left: 620px; background: var(--paper); }
  .card-shape { position: absolute; inset: 0; }

  .front-brand {
    position: absolute;
    left: 36px;
    top: 168px;
    width: 196px;
    text-align: center;
    font-weight: 700;
    font-size: 50px;
    letter-spacing: 2px;
    color: var(--ink);
    line-height: 1;
  }
  .divider {
    position: absolute;
    left: 252px;
    top: 80px;
    width: 1.5px;
    height: 170px;
    background: var(--rule);
  }
  .details {
    position: absolute;
    left: 272px;
    top: 82px;
    color: var(--ink);
  }
  .person-name { font-weight: 700; font-size: 22px; line-height: 1.1; }
  .person-role { font-size: 13px; margin-top: 2px; }
  .address { font-size: 13.5px; line-height: 1.3; margin-top: 8px; color: #1f2428; }
  .contact-list { list-style: none; margin-top: 8px; }
  .contact-list li {
    display: flex;
    align-items: center;
    gap: 7px;
    font-size: 13.5px;
    line-height: 1.45;
    color: #1f2428;
  }
  .contact-icon { width: 12px; height: 12px; flex: none; }

  .back-brand {
    position: absolute;
    left: 0; right: 0;
    top: 176px;
    text-align: center;
    font-weight: 700;
    font-size: 76px;
    letter-spacing: 3px;
    color: var(--paper);
    line-height: 1;
    padding-left: 70px;
  }
</style>
</head>
<body>

  <section class="card card-front" aria-label="Card front with contact details">
    <svg class="card-shape" viewBox="0 0 540 308" preserveAspectRatio="none">
      <ellipse cx="262" cy="160" rx="330" ry="176" fill="var(--paper)" transform="rotate(-14 262 160)"/>
    </svg>
    <div class="front-brand">VOMRA</div>
    <div class="divider"></div>
    <div class="details">
      <p class="person-name">Ethan Mercer</p>
      <p class="person-role">Co-Founder</p>
      <p class="address">42-44 Harbour Lane Westmead<br>NSW 2145 Australia</p>
      <ul class="contact-list">
        <li>
          <svg class="contact-icon" viewBox="0 0 12 12"><circle cx="6" cy="6" r="6" fill="var(--ink)"/><path d="M4 3.2c.4-.3.8-.2 1 .2l.4.8c.1.3 0 .5-.2.7l-.3.2c.3.6.7 1.1 1.3 1.4l.3-.3c.2-.2.4-.2.7-.1l.8.4c.4.2.4.6.1 1-.5.6-1.2.7-2 .2C4.9 7.1 4 6 3.6 4.8c-.2-.6 0-1.2.4-1.6z" fill="#fff"/></svg>
          (555) 214-8830
        </li>
        <li>
          <svg class="contact-icon" viewBox="0 0 12 12"><circle cx="6" cy="6" r="6" fill="var(--ink)"/><circle cx="6" cy="6" r="3.6" fill="none" stroke="#fff" stroke-width=".8"/><path d="M2.4 6h7.2M6 2.4c-1.4 1.8-1.4 5.4 0 7.2M6 2.4c1.4 1.8 1.4 5.4 0 7.2" fill="none" stroke="#fff" stroke-width=".7"/></svg>
          www.vomra.com.au
        </li>
        <li>
          <svg class="contact-icon" viewBox="0 0 12 12"><rect x="0" y="2" width="12" height="8.5" rx="1" fill="var(--ink)"/><path d="M.8 2.8 6 7l5.2-4.2" fill="none" stroke="#fff" stroke-width=".9"/></svg>
          admin@vomra.com.au
        </li>
      </ul>
    </div>
  </section>

  <section class="card card-back" aria-label="Card back with company name">
    <svg class="card-shape" viewBox="0 0 540 308" preserveAspectRatio="none">
      <ellipse cx="272" cy="150" rx="330" ry="176" fill="var(--ink)" transform="rotate(-14 272 150)"/>
    </svg>
    <div class="back-brand">VOMRA</div>
  </section>

</body>
</html>
```